Yard sign

Looking for a yard sign. <br/>Something simple, name, number. <br/>Large text, readable from 50 feet away. <br/><br/>18 x 24 inches.

Target Market(s)

Potential homeowners thinking about going solar.

Colors

Designer to choose colors to be used in the design.

Requirements
Must have
• "WE'VE GONE SOLAR!"
Nice to have
• We are a solar company, we would like a design that compliments the homeowners decision that they went solar and encourages others to do the same.

```html
<!DOCTYPE html>
<html lang="en">
<head>
<meta charset="utf-8">
<title>We've Gone Solar – Yard Sign</title>
<link rel="stylesheet" href="https://fonts.googleapis.com/css2?family=Montserrat:wght@600;700&display=swap">
<style>
  :root {
    --sun-orange: #f39025;
    --sign-white: #ffffff;
  }
  * { margin: 0; padding: 0; box-sizing: border-box; }
  html, body {
    width: 1200px;
    height: 900px;
    overflow: hidden;
    background: var(--sign-white);
  }
  .yard-sign {
    position: relative;
    width: 1200px;
    height: 900px;
    background: var(--sign-white);
    font-family: "Montserrat", "Century Gothic", sans-serif;
    overflow: hidden;
  }
  .headline {
    position: absolute;
    left: 0;
    width: 1200px;
    text-align: center;
    color: var(--sun-orange);
    font-weight: 700;
    line-height: 1;
    text-transform: uppercase;
  }
  .headline-top {
    top: 118px;
    font-size: 142px;
    letter-spacing: 2px;
  }
  .headline-main {
    top: 250px;
    font-size: 250px;
    letter-spacing: 4px;
  }
  .contact-band {
    position: absolute;
    left: 0;
    top: 0;
    width: 1200px;
    height: 900px;
  }
  .brand {
    position: absolute;
    left: 105px;
    top: 650px;
    display: flex;
    align-items: center;
    gap: 14px;
    color: var(--sign-white);
  }
  .brand-mark {
    width: 44px;
    height: 44px;
    border-radius: 50%;
    background: var(--sign-white);
    flex: none;
  }
  .brand-name {
    font-weight: 700;
    font-size: 34px;
    line-height: 1.05;
    text-transform: uppercase;
  }
  .phone {
    position: absolute;
    left: 452px;
    top: 618px;
    color: var(--sign-white);
    font-weight: 700;
    font-size: 98px;
    line-height: 1;
    letter-spacing: 1px;
  }
  .website {
    position: absolute;
    left: 458px;
    top: 733px;
    color: var(--sign-white);
    font-weight: 700;
    font-size: 40px;
    line-height: 1;
    letter-spacing: 1.5px;
  }
</style>
</head>
<body>
  <main class="yard-sign">
    <h1 class="headline headline-top">We've Gone</h1>
    <p class="headline headline-main">Solar!</p>

    <svg class="contact-band" viewBox="0 0 1200 900" aria-hidden="true">
      <path d="M0 487 Q560 590 1200 462 L1200 900 L0 900 Z" fill="var(--sun-orange)"/>
    </svg>

    <div class="brand">
      <span class="brand-mark"></span>
      <span class="brand-name">Brightline<br>Solar</span>
    </div>
    <p class="phone">555-014-2736</p>
    <p class="website">www.brightlinesolar.com</p>
  </main>
</body>
</html>
```